Corvane Holdings , new business card design

investment firm with corporate clients . need double sided business card , vertical and horizontal options ,logo must be clear. prefer pantone colors only and sharp design. website also www.corvane.ae

Khalid Bin Tarrafi
Managing Director
Tel. +971 4 387 2940
Mobile +971 50 518 2403
khalid@corvane.ae
Q-Span Plaza, officw 18-B07, Warqa Gardens, Dubai

Contact Information for Business Card

Khalid Bin Tarrafi
Managing Director

Font styles to use
Serif

Colors

Designer to choose colors to be used in the design.

```html
<!DOCTYPE html>
<html lang="en">
<head>
<meta charset="utf-8">
<title>Corvane Holdings – Business Card</title>
<link rel="stylesheet" href="https://fonts.googleapis.com/css2?family=Jost:wght@300;400;500&display=swap">
<style>
  :root {
    --backdrop: #e4e5e7;
    --card-blue: #3a6289;
    --card-white: #f6f6f5;
    --ink: #3c3c3e;
    --accent: #4a78a8;
    --rule: #6f93ba;
    --on-blue: #f4f6f9;
  }
  * { margin: 0; padding: 0; box-sizing: border-box; }
  html, body {
    width: 1200px; height: 900px; overflow: hidden;
    background: var(--backdrop);
    font-family: "Jost", sans-serif;
  }
  .canvas {
    position: relative; width: 1200px; height: 900px;
  }
  .card {
    position: absolute;
    width: 520px; height: 297px;
    box-shadow: 0 6px 18px rgba(0,0,0,0.12);
  }
  .card--front {
    left: 60px; top: 180px;
    background: var(--card-blue);
    display: flex; align-items: center; justify-content: center;
  }
  .card--back {
    left: 620px; top: 423px;
    background: var(--card-white);
    display: flex; align-items: center;
  }
  .wordmark {
    display: flex; align-items: center; gap: 14px;
    font-weight: 300; text-transform: uppercase;
  }
  .wordmark__square { width: 12px; height: 12px; }
  .wordmark__name { line-height: 1.15; }
  .wordmark__line { display: block; }
  .wordmark--front { color: var(--on-blue); }
  .wordmark--front .wordmark__square { background: var(--on-blue); }
  .wordmark--front .wordmark__line:first-child { font-size: 40px; letter-spacing: 14px; }
  .wordmark--front .wordmark__line:last-child { font-size: 13px; letter-spacing: 12px; }
  .wordmark--back { color: var(--ink); }
  .wordmark--back .wordmark__square { background: var(--ink); }
  .wordmark--back .wordmark__line:first-child { font-size: 24px; letter-spacing: 8px; }
  .wordmark--back .wordmark__line:last-child { font-size: 8px; letter-spacing: 7px; }
  .card__logo-area {
    width: 250px; display: flex; justify-content: center;
  }
  .card__divider {
    width: 1px; height: 150px; background: var(--rule);
  }
  .contact {
    padding-left: 26px; color: var(--ink);
    font-size: 11px; line-height: 1.35; font-weight: 400;
  }
  .contact__name {
    color: var(--accent); font-weight: 500; font-size: 13px;
    text-transform: uppercase; letter-spacing: 0.3px;
  }
  .contact__role { margin-bottom: 12px; }
  .contact__address { margin-bottom: 12px; }
  .contact__row { display: flex; align-items: center; gap: 6px; }
  .contact__icon { width: 9px; height: 9px; flex: none; }
</style>
</head>
<body>
<main class="canvas">
  <section class="card card--front" aria-label="Card front">
    <div class="wordmark wordmark--front">
      <span class="wordmark__square"></span>
      <span class="wordmark__name">
        <span class="wordmark__line">Corvane</span>
        <span class="wordmark__line">Holdings</span>
      </span>
    </div>
  </section>

  <section class="card card--back" aria-label="Card back">
    <div class="card__logo-area">
      <div class="wordmark wordmark--back">
        <span class="wordmark__square"></span>
        <span class="wordmark__name">
          <span class="wordmark__line">Corvane</span>
          <span class="wordmark__line">Holdings</span>
        </span>
      </div>
    </div>
    <div class="card__divider"></div>
    <div class="contact">
      <p class="contact__name">Khalid Bin Tarrafi</p>
      <p class="contact__role">Managing Director</p>
      <p class="contact__address">Q-Span Plaza, officw 18-B07,<br>Warqa Gardens, Dubai</p>
      <p class="contact__row">
        <svg class="contact__icon" viewBox="0 0 10 10"><path d="M2 1l2 2-1 1.2c.6 1.2 1.5 2.1 2.8 2.8L7 6l2 2-1.3 1.3C4.5 9 1 5.5.7 2.3z" fill="var(--accent)"/></svg>
        +971 4 387 2940
      </p>
      <p class="contact__row">
        <svg class="contact__icon" viewBox="0 0 10 10"><rect x="2.5" y="0.5" width="5" height="9" rx="1" fill="none" stroke="var(--accent)"/><rect x="4" y="7.5" width="2" height="1" fill="var(--accent)"/></svg>
        +971 50 518 2403
      </p>
      <p class="contact__row">
        <svg class="contact__icon" viewBox="0 0 10 10"><rect x="0.5" y="2" width="9" height="6" fill="none" stroke="var(--accent)"/><path d="M.5 2L5 5.5 9.5 2" fill="none" stroke="var(--accent)"/></svg>
        khalid@corvane.ae
      </p>
    </div>
  </section>
</main>
</body>
</html>
```